Simple templates for management consulting firm

Vireo Advisors is a management consulting firm based in the DC area. We have all the basic templates but would like to tweak them so they look consistent.

Check us out at www.vireoadvisors.example

For this project we would like to get
a tweaked powerpoint template (header should be up)
a letter template for letters
a fax template

Current templates and our logo are attached.
Updates

We just increased the budget of this project.

We got questions about the project. Here are our thoughts on this one:

Please include the logo into the fax template. If you find improvements in the layout then feel free to make those. Let's not overthink this too much. Keep it simple :)

We like The powerpoint concept as is. The slide titles are for some reasons on the bottom. It seems to irritate some folks. If you can switch the slide titles to the top, keep the look and feel of the slides and work in the logo then that would be fantastic.

The letter head should include the following

Vireo Advisors, LLC Box 5827, Great Falls, VA 20471 Phone 703 555-0148, Fax 703 555 0193, www.vireoadvisors.example and the logo.

Again, let's keep it simple.

Thank you for considering this project.

We just realize that we are not necessarily inisting to use the red in the slides.
Any approach that would work with the logo will be considered.

Thanks for your creativity.

Target Market(s)

tech companies, Meridian 400, venture capitalists

Industry/Entity Type

Management Consulting

Requirements
Must have
• Keep it simple please

```html
<!DOCTYPE html>
<html lang="en">
<head>
<meta charset="utf-8">
<title>Vireo Advisors – Slide Templates</title>
<link href="https://fonts.googleapis.com/css2?family=Fira+Sans:wght@800&family=Fira+Sans+Condensed:ital,wght@0,400;0,600;1,600;1,700&family=Fira+Sans+Extra+Condensed:wght@400&display=swap" rel="stylesheet">
<style>
  :root {
    --page: #ffffff;
    --slide-light: #f6f6f6;
    --slide-mid: #dcdcdc;
    --slide-edge: #c4c4c4;
    --title-grey: #8c8c8c;
    --ink: #4a4a4a;
    --ink-dark: #333333;
    --gold: #f0c030;
    --gold-deep: #c9931a;
    --gold-light: #fbe08a;
    --rule: #9a9a9a;
    --logo-grey: #6a6a6a;
  }
  * { box-sizing: border-box; margin: 0; padding: 0; }
  html, body { width: 869px; height: 1200px; overflow: hidden; background: var(--page); }
  body { position: relative; font-family: "Fira Sans Condensed", "Arial Narrow", sans-serif; color: var(--ink); }

  .slide {
    position: absolute; left: 0; width: 869px; overflow: hidden;
    background: radial-gradient(ellipse at 50% 40%, var(--slide-light) 0%, var(--slide-mid) 70%, var(--slide-edge) 100%);
  }
  .slide--process { top: 0; height: 590px; }
  .slide--case { top: 606px; height: 594px; }

  .slide-title {
    position: absolute; font-family: "Fira Sans", sans-serif; font-weight: 800;
    font-size: 68px; letter-spacing: -1px; color: var(--title-grey);
    text-shadow: 2px 3px 3px rgba(0,0,0,0.35), -1px -1px 0 rgba(255,255,255,0.6);
    line-height: 1; white-space: nowrap;
  }
  .title-bar {
    position: absolute; height: 10px;
    background: linear-gradient(to bottom, var(--gold-light), var(--gold) 50%, var(--gold-deep));
    box-shadow: 2px 3px 3px rgba(0,0,0,0.4);
  }
  .brand {
    position: absolute; display: flex; align-items: center; gap: 7px;
    font-family: "Fira Sans Condensed", sans-serif; font-weight: 600;
    font-size: 19px; color: var(--logo-grey); white-space: nowrap;
  }
  .brand-dot { width: 30px; height: 30px; border-radius: 50%; background: var(--gold); }

  .step {
    position: absolute; height: 69px; border-radius: 8px;
    border: 2px solid #b8b8b8;
    background: linear-gradient(to bottom, #e6e0c8, #d8c27a 45%, #b49e5a);
    box-shadow: 2px 3px 5px rgba(0,0,0,0.35);
    display: flex; align-items: center; justify-content: center;
    font-family: "Fira Sans Condensed", sans-serif; font-weight: 600;
    font-size: 42px; color: #555; text-shadow: 1px 1px 1px rgba(255,255,255,0.5);
  }
  .step-notes {
    position: absolute; font-style: italic; font-weight: 700;
    font-size: 13px; line-height: 15px; color: var(--ink); white-space: nowrap;
  }
  .step-notes--right { text-align: right; }
  .flow-arrow { position: absolute; }

  .footer-rule { position: absolute; height: 1px; background: var(--rule); }
  .copyright {
    position: absolute; left: 0; width: 100%; text-align: center;
    font-size: 13.5px; line-height: 12px; color: var(--ink-dark); white-space: nowrap;
  }

  .case-heading {
    position: absolute; left: 64px; font-style: italic; font-weight: 700;
    font-size: 31px; color: var(--ink-dark); line-height: 1;
  }
  .case-body {
    position: absolute; left: 84px;
    font-family: "Fira Sans Extra Condensed", "Arial Narrow", sans-serif;
    font-size: 20px; line-height: 22.5px; color: var(--ink); white-space: nowrap;
  }
</style>
</head>
<body>

<section class="slide slide--process">
  <h1 class="slide-title" style="left:55px; top:20px;">Mastering the Sale</h1>
  <div class="title-bar" style="left:55px; top:93px; width:580px;"></div>
  <div class="brand" style="left:652px; top:80px;"><span class="brand-dot"></span>Vireo Advisors</div>

  <div class="step" style="left:88px; top:174px; width:136px;">Assess</div>
  <p class="step-notes" style="left:241px; top:184px;">What problems do we solve?<br>Who has these problems?<br>What do we need to be successful?</p>

  <svg class="flow-arrow" style="left:128px; top:252px;" width="100" height="100" viewBox="0 0 100 100">
    <defs>
      <linearGradient id="arrowGold" x1="0" y1="0" x2="1" y2="1">
        <stop offset="0" stop-color="#fbe08a"/><stop offset="0.5" stop-color="#f0c030"/><stop offset="1" stop-color="#c9931a"/>
      </linearGradient>
    </defs>
    <path d="M8 4 C2 40 30 62 62 60 L62 44 L92 66 L62 92 L62 76 C22 78 -4 48 8 4 Z" fill="url(#arrowGold)" stroke="#b88a20" stroke-width="1"/>
  </svg>

  <div class="step" style="left:231px; top:280px; width:160px;">Prepare</div>
  <p class="step-notes" style="left:408px; top:292px;">What is our business model?<br>Who are our specific targets?<br>Is our process repeatable?</p>

  <svg class="flow-arrow" style="left:300px; top:356px;" width="100" height="100" viewBox="0 0 100 100">
    <path d="M8 4 C2 40 30 62 62 60 L62 44 L92 66 L62 92 L62 76 C22 78 -4 48 8 4 Z" fill="url(#arrowGold)" stroke="#b88a20" stroke-width="1"/>
  </svg>

  <div class="step" style="left:403px; top:383px; width:161px;">Capture</div>
  <p class="step-notes step-notes--right" style="left:560px; top:395px; width:183px;">How do we build relationships<br>with new clients?<br>How do we grow relationships<br>with existing clients?</p>

  <div class="footer-rule" style="left:25px; top:537px; width:762px;"></div>
  <p class="copyright" style="top:545px;">Copyright © 2012 by Vireo Advisors, LLC. All rights reserved. This document contains confidential and proprietary information and may not be<br>reproduced, in whole or in part, without express written permission from Vireo Advisors, LLC.</p>
</section>

<section class="slide slide--case">
  <h1 class="slide-title" style="left:64px; top:24px;">Case1</h1>
  <div class="title-bar" style="left:65px; top:91px; width:580px;"></div>
  <div class="brand" style="left:662px; top:80px;"><span class="brand-dot"></span>Vireo Advisors</div>

  <h2 class="case-heading" style="top:119px;">Situation:</h2>
  <p class="case-body" style="top:154px;">The owners of a private software company had spent about ten years building a software and<br>services organization. They had collected over the years some high profile clients. Of all of these<br>clients, one customer engagement was very successful and highly profitable. This engagement<br>had benefited from a strong internal champion who did all the work to obtain buy-in and<br>sponsorship. Most of the other engagements with similar clients were not approaching the<br>same level of business impact and financial rewards. They didn’t know how to repeat success.</p>

  <h2 class="case-heading" style="top:297px;">Approach:</h2>
  <p class="case-body" style="top:332px;">We developed an enterprise grade account management process. We created a more strategic<br>approach to their solution tying in better to the pain of their clients. Also, we introduced the<br>concept of executive level selling.</p>

  <h2 class="case-heading" style="top:419px;">Results:</h2>
  <p class="case-body" style="top:454px;">The solution increased in value from $2M to $17M per customer. The company focused on<br>strategic markets and was able to create repeat business based on the ability to articulate its<br>value proposition clear and concise to various stakeholders.</p>

  <div class="footer-rule" style="left:38px; top:533px; width:760px;"></div>
  <p class="copyright" style="top:541px;">Copyright © 2012 by Vireo Advisors, LLC. All rights reserved. This document contains confidential and proprietary information and may not be<br>reproduced, in whole or in part, without express written permission from Vireo Advisors, LLC.</p>
</section>

</body>
</html>
```